Luxurious Product label and box for all natural skincare product. + 30AUD tip to winner.

What I require.
1.     One product label and one-box design.
2.     I must have a mock-up of the bottle with the attached label and the box.
 
I have supplied the following files for the designers to use.
1.     Brand logo file. (logo.zip)
2.     Slogan file. (slogan.psd)
3.     Slogan script file. (italianno.regular.ttf)
4.     Bottle image file. (60ml_moisturiser_bottle.png)
5.     Icon bar file. (Icon_bar_en.zip)
 
Label and box Design
I am interested in your unique design concepts and colors, so please feel free to be creative.
1.     Brand name: Velia
2.     You can use your own choice of colors in your design. I would prefer two colors (excluding logo and slogan colors), although more colors are acceptable for the right design.
3.     Label and box to have a background color or pattern.
4.     I would like the icon bar to wrap around the bottom of the label and box, covering the full width of all sides of the box.
5.     The height of the icon bar should be about 7mm to 10mm high.   
6.     The hex code for the icon bar color is #EDD6D4. The color of the icons can be any color the designer chooses.
7.     The positioning of the icons are as follows.
a)     The front panel has three icons. From left to right, they are; 100% Vegan, Product of Australia, and 100% Natural.
b)     The left side panel has three icons. From the front of the label/box to the back of the label/box, they are; Cruelty-Free, Ethical & Sustainable, and Please Recycle.
c)     The right side panel has only one icon situated at the front of the right side of the label/box. The icon is 6 Months Once Open.
 
Label.
1.     The label will be a three-panel label.
2.     The label will contain text in all three panels; however, only the text for the front panel of the label is supplied in this brief. For now, use Lorem Ipsum placeholder text to fill spaces.
3.     The final text will be provided to the winning designer so they can apply the text to the left and right panels of the label.
4.     Label size. Width 104mm x Height 83mm.
5.     The final design file must include bleed and cut lines.
 
Box.
1.     The box will contain text on all four sides; however, only the text for the front of the box is supplied in this brief. For now, use Lorem Ipsum placeholder text to fill spaces.
2.     The final text will be provided to the winning designer so they can apply the text to the left and right sides and the back of the box.
3.     The box size is 40mm wide x 40mm deep x 140mm high.
4.     The final design file must include bleed and cut lines.
 
Front Panel wording.
1.     Logo.
2.     Slogan.
3.     Moisturiser.
4.     Hydrate & Nourish.
5.     Hyaluronic Acid, Desert Lime & Green Tea.
6.     All Skin Types - Dry – Dehydrated.
7.     Icon bar.
8.     60mL
 
Bottle size
60ml White Bottle – 13.5cm High x 3.5cm Wide.

Target Market(s)

Beauty-minded Asian consumers between the age of 32 and 75 who take a proactive approach in maintaining younger-looking skin. Those who already know the danger of damaged skin caused by skincare containing harsh chemicals, and therefore choose effective natural/organic solutions to meet their skincare needs. Those who wish a more radiant glow and youthful appearance to their skin. Usually, a two-income middle to high-income bracket couple with a mindset for health and beauty.

Industry/Entity Type

Beauty and skincare.

Font styles to use
Other font styles liked:
• Logo and slogan script supplied. Designer to choose all other font or script.

Colors

Designer to choose colors to be used in the design.

Requirements
Must have
• A mock-up label on the bottle and a mock-up box. My logo and slogan are already designed with my chosen font and color.
Nice to have
• I like soft pastel colors with perhaps a small amount of stronger color.

```html
<!DOCTYPE html>
<html lang="en">
<head>
<meta charset="utf-8">
<title>Velia Moisturiser – Three-Panel Label</title>
<link href="https://fonts.googleapis.com/css2?family=Montserrat:wght@500;600;800&family=Roboto+Condensed:wght@400;700&family=Oswald:wght@300&family=Italianno&display=swap" rel="stylesheet">
<style>
  :root{
    --page:#ffffff;
    --cream:#f6f4ea;
    --green:#1f7a34;
    --green-dark:#1d6b2f;
    --mint:#d6ebdb;
    --pink:#edd6d4;
    --gold:#b9802a;
    --body:#8b5e3c;
    --icon:#8d7d7d;
    --white:#ffffff;
  }
  *{box-sizing:border-box;margin:0;padding:0}
  html,body{width:716px;height:1200px;overflow:hidden;background:var(--page)}
  .label{position:absolute;left:38px;top:344px;width:640px;height:509px;background:var(--cream);box-shadow:0 1px 4px rgba(0,0,0,.12);overflow:hidden}
  .abs{position:absolute}
  .col{position:absolute;width:160px}
  .col-left{left:16px}
  .col-right{left:464px}
  .heading{font-family:'Montserrat',sans-serif;font-weight:600;font-size:12px;color:var(--green);text-align:center;line-height:1}
  .copy{font-family:'Roboto Condensed',sans-serif;font-size:8.1px;line-height:10.4px;color:var(--body);text-align:justify;hyphens:auto}
  .brand{left:200px;top:30px;width:240px;text-align:center;font-family:'Montserrat',sans-serif;font-weight:600;font-size:62px;line-height:78px;color:var(--gold);letter-spacing:1px}
  .slogan-row{left:187px;top:126px;width:265px;display:flex;align-items:center;gap:6px}
  .slogan-row .rule{flex:1;height:1px;background:var(--green)}
  .slogan{font-family:'Italianno',cursive;font-size:30px;line-height:34px;color:var(--green)}
  .product{left:190px;top:190px;width:260px;text-align:center;font-family:'Montserrat',sans-serif;font-weight:800;font-size:29px;line-height:32px;color:var(--green);letter-spacing:.5px}
  .claim{left:206px;top:229px;width:227px;height:39px;background:var(--mint);text-align:center;font-family:'Oswald',sans-serif;font-weight:300;font-size:25px;line-height:39px;color:var(--green);letter-spacing:1.5px}
  .fruit-mark{left:301px;top:287px;width:42px;height:32px;border-radius:50% 50% 45% 45%;background:linear-gradient(135deg,#2e8a3e,#1f6e30)}
  .key-line{left:190px;width:260px;text-align:center;font-family:'Montserrat',sans-serif;font-weight:500;font-size:10.4px;line-height:12px;color:#7a6a5e}
  .key-line b{color:var(--green);font-weight:600}
  .address{font-family:'Roboto Condensed',sans-serif;font-weight:700;font-size:8px;line-height:10.6px;color:var(--body);text-align:center}
  .icon-bar{left:0;top:377px;width:640px;height:76px;background:var(--pink)}
  .badge{position:absolute;top:8px;width:60px;margin-left:-30px;text-align:center}
  .badge svg,.badge .mark{display:block;margin:0 auto;width:36px;height:36px}
  .badge .mark{border-radius:50%;background:#d9bfbc}
  .badge p{margin-top:4px;font-family:'Montserrat',sans-serif;font-weight:600;font-size:7.4px;line-height:9px;color:var(--icon)}
  .base-bar{left:0;top:453px;width:640px;height:56px;background:var(--green-dark);color:var(--white)}
  .base-script{font-family:'Italianno',cursive;font-size:27px;line-height:56px;position:absolute;top:0}
  .volume{position:absolute;left:0;width:640px;text-align:center;font-family:'Montserrat',sans-serif;font-weight:500;font-size:11.5px;line-height:56px}
</style>
</head>
<body>
<main class="label">
  <section class="col col-left" style="top:35px">
    <h2 class="heading">What is Lorem Ipsum?</h2>
    <p class="copy" style="margin-top:9px">Lorem Ipsum is simply dummy text of the printing and typesetting industry. Lorem Ipsum has been the industry's standard dummy text ever since the 1500s, when an unknown printer took a galley of type and scrambled it to make a type specimen book. It has survived not only five centuries, but also the leap into electronic typesetting, remaining essentially unchanged. It was popularised in the 1960s with the release of Letraset sheets containing.</p>
    <h2 class="heading" style="margin-top:14px">Moisturiser Information</h2>
    <p class="copy" style="margin-top:9px">Lorem Ipsum is simply dummy text of the printing and typesetting industry. Lorem Ipsum has been the industry's standard dummy text ever since the 1500s, when an unknown printer took a galley of type and scrambled it to make a type specimen book. It has survived not only five centuries, but also the leap into electronic typesetting, remaining essentially unchanged. It was popularised in the 1960s with the release of Letraset sheets containing.</p>
  </section>

  <div class="abs brand">Velia</div>
  <div class="abs slogan-row"><span class="rule"></span><span class="slogan">grown by nature</span><span class="rule"></span></div>
  <h1 class="abs product">MOISTURISER</h1>
  <div class="abs claim">HYDRATE &amp; NOURISH</div>
  <div class="abs fruit-mark" role="img" aria-label="Desert lime and green tea leaf icon"></div>
  <p class="abs key-line" style="top:333px">Hyaluronic Acid <b>+</b> Desert Lime <b>+</b> Green Tea</p>
  <p class="abs key-line" style="top:350px">All Skin Types <b>+</b> Dry <b>+</b> Dehydrated</p>

  <section class="col col-right" style="top:35px">
    <h2 class="heading">Directions</h2>
    <p class="copy" style="margin-top:9px">Lorem Ipsum is simply dummy text of the printing and typesetting industry. Lorem Ipsum has been the industry's standard dummy text ever since the 1500s, when an unknown printer took a galley of type and scrambled it to make a type specimen book. It has survived not only five centuries, but also the leap into electronic typesetting, remaining essentially unchanged. It was popularised in the 1960s with the release of Letraset sheets containing.</p>
    <h2 class="heading" style="margin-top:14px">Ingredients</h2>
    <p class="copy" style="margin-top:9px">Lorem Ipsum is simply dummy text of the printing and typesetting industry. Lorem Ipsum has been the industry's standard dummy text ever since the 1500s, when an unknown printer took a galley of type and scrambled it to make a type specimen book. It has survived not only five centuries, but also the leap into electronic typesetting, remaining essentially unchanged. It was popularised in the 1960s with the release of Letraset sheets containing.</p>
    <h2 class="heading" style="margin-top:14px">Manufactured by</h2>
    <p class="address" style="margin-top:6px">18 Wattle Grove Road<br>Lorem ipsum City | Lorem ipsum 466200<br>www.veliaskincare.example</p>
  </section>

  <section class="abs icon-bar">
    <div class="badge" style="left:37px"><div class="mark" role="img" aria-label="Rabbit icon"></div><p>Cruelty<br>Free</p></div>
    <div class="badge" style="left:94px"><div class="mark" role="img" aria-label="Globe with leaf icon"></div><p>Ethical &amp;<br>Sustainable</p></div>
    <div class="badge" style="left:153px">
      <svg viewBox="0 0 36 36" fill="none" stroke="var(--icon)" stroke-width="2" stroke-linejoin="round">
        <path d="M14 8 L18 3 L22 8"/><path d="M18 3 L26 17"/><path d="M29 19 L33 27 L26 27"/><path d="M33 27 L17 31"/><path d="M12 33 L5 28 L10 22"/><path d="M5 28 L11 15"/>
      </svg><p>Please<br>Recycle</p></div>
    <div class="badge" style="left:234px">
      <svg viewBox="0 0 36 36" fill="none" stroke="var(--icon)" stroke-width="2.2" stroke-linejoin="round"><path d="M18 33 L5 16 C1 10 5 3 11 4 C15 5 18 9 18 12 C18 9 21 5 25 4 C31 3 35 10 31 16 Z"/></svg>
      <p>100%<br>Vegan</p></div>
    <div class="badge" style="left:315px"><div class="mark" role="img" aria-label="Kangaroo icon"></div><p>Product of<br>Australia</p></div>
    <div class="badge" style="left:396px">
      <svg viewBox="0 0 36 36" fill="none" stroke="var(--icon)" stroke-width="2" stroke-linejoin="round">
        <path d="M18 30 C12 24 12 12 18 4 C24 12 24 24 18 30 Z"/><path d="M17 30 C9 31 3 26 2 18 C10 17 16 22 17 30 Z"/><path d="M19 30 C27 31 33 26 34 18 C26 17 20 22 19 30 Z"/>
      </svg><p>100%<br>Natural</p></div>
    <div class="badge" style="left:544px">
      <svg viewBox="0 0 36 36" fill="none" stroke="var(--icon)" stroke-width="2" stroke-linejoin="round">
        <path d="M5 8 L31 3"/><path d="M6 13 H30 V33 H6 Z"/>
        <text x="18" y="28" text-anchor="middle" font-family="Montserrat, sans-serif" font-size="10" font-weight="600" fill="var(--icon)" stroke="none">6 M</text>
      </svg><p>6 Months<br>Once Open</p></div>
  </section>

  <footer class="abs base-bar">
    <span class="base-script" style="left:26px">hydrate &amp; nourish</span>
    <span class="volume">2.1fl.oz. | 60mL</span>
    <span class="base-script" style="left:485px">grown by nature</span>
  </footer>
</main>
</body>
</html>
```